SaaS / Consulting / Solution website redesign

We need a website design that:
- Is completely different than our current design : https://plumvessel.net
- Has a very minimal amount of copy
- Changes our positioning from a SaaS application to a solutions company. Solutions company means that we help our customers solve their problems with consulting, training, and tools. An example of a solutions company is here: https://oldpages.example/web/20130111103320/http://www.brindlework.com:80/
- Does not make us look like a start up
- Is more people oriented than technology oriented

We need a designer that:
- Is a rebel at heart
- Is a minimalist
- Tells us why our current site sucks
- Can disagree with us
- Can also do copywriting or already has a copywriter that can help
- Is ok with saying we have capability that we don't in order to see if people actually want that
- Can understand the difference between our grand vision and where we need to focus ourselves today in order to get there

Who we are:
- Entrepreneurs
- Programmers
- Consultants
- Investors

Here's our design goals:
#1 Get customers, investors, employers, and partners excited about our unique and clearly articulated value proposition
#2 Get people to contact us asking for help with their programs
#3 Position ourselves as an expert in the skills based volunteering, mentorship, and group collaboration
#4 Make it easy for people, who already know who we are, to register online

What our grand vision is:
- Create a marketplace where any person can go to our site and find time with anyone they need to meet with. Whether that is their hair stylist, school advisor, parent of your kids class, dentist, attorney, etc.

What will you get if you win:
- In addition to the prize of this project we will have many landing pages and other revisions we will need in the future. We currently don't have a designer or copywriter and need to add that capability to our team

Who do we need to appeal to:
- Directors that are launching innovative programs inside organizations
- IT personnel who are trying to disqualify our technology so they don't have to support it or deal with it when it doesn't go well
- Enterprise IT architects who don't want our product being on its own island within their organization totally incompatible with everything else. Architects which are trying to assess how our platform will co-exist with all their other platforms
- Vice Presidents who want to help their directors understand that we don't have enough experience to help them
- Program managers who have to juggle a million things and need a tool that actually helps instead of confuses them and adds more work for them.
- Program managers & directors that have been given ambiguous goals by their board of directors like "improve retention, increase engagement, create innovation, get people to collaborate." And who have no idea where to start or how to deliver on things like that.
- Program managers, directors, and vice presidents that are trying to understand how our technology and services fit into their existing technology and capability
- Employees who are bored and uninspired with their current tools and are hoping for some excitement in their life. Kind of like candy or a double espresso.
- Investors who think, our company like all the rest, are going to waste their money and make them look like a fool

Other information:
-The CSS and html needs to be responsive

-Our registration onboarding flow needs to collect this information:
User first name
user last name
user email
(verify their email)
user phone number
(verify their phone number)
User profile image (optional)
User profile summary (optional, like a bio, freeform text fiels)
If applicable: Register their organization
Organization name
Organization image (optional)
Account Mailing address
account Billing address (could be same as mailing address)
account Billing email address (could be same as user address)
account Product selection (pricing tier)
account Credit card information

The designs I am getting are a good start but they are only the front page. I just want you to know that I am expecting and need more than a landing page to complete the design. I will likely need a page that outlines the benefits and features of the product itself, how its different than our competitors, which will not be on the front page. I will need a registration flow. I will need a blog page design so we can post blog articles, I will need a team page, a page that goes into detail on our training, our services. I will likely need a page that shows all news and media we have been in. I need to show customer and user quotes, case studies, a way to contact us, partners, general resources like on collaboration, product tutorials, customers. I need the site to address a comprehensive set of needs. I need that design to be consistent and thorough. I know what PlateHarbor is. I'm not using because I need more than a template that was customized. I need to be unique and match our brand thoughtfully, beautifully, and artistically. Someone asked me a question about how Murmly is similar to our tool in the way it is referred by end users and purchased by managers. Our website needs to primarily talk to the managers as I explained in the brief but it needs to appear cool and exciting to our end-users without focusing on the technology too much. Murmly is a tool that teams use to collaborate in small and large enterprises. The value prop for them is that communication is easier. But they don't put that on their website. Why? Because the users of the technology won't go to the website to find out information on it, they get their information from someone who is using it and demos it to them. When Ines tells her manager Otto "Lets get murmly, Ruth is using it at her company and its great" Ines's manager doesn't know anything about murmly so she promptly googles it. The most important thing from Ines's perspective is that Otto agrees to try it out. Otto's biggest concern is that productivity will be enhanced to degraded. Murmly knows this and so on the front page they know they are talking to Otto NOT Ines because Ines is already sold on it and doesn't need to get sold on the website. Ines is end user. Otto is the purchaser. We have the same problem and so our end users are not the ones purchasing our product, their managers are purchasing our product. We get referred by our end users and vetted by their managers. Hope this helps! Thank you for looking at this project!  Added Wednesday, June 7, 2017

Another observation I am having about the designs being submitted. I believe we used the animations on our current website because animations / cartoons connect with the "inner child" in our users. Whatever that means :-). I think it's what makes our brand fun. I have a hard time imagining that we could make the design fun looking without animations but I'm sure it can be achieved. I also recognize that blending pictures of real people and animations is hard. So either we must masterfully blend them, use only animations, or make the real people have a LOT of fun! So far most of the designs while achieve the goal of appealing to the serious Vice Presidents and directors, they are not doing a good job at appealing to the overworked program managers and bored employees. There seems to stand another challenge with animations which is animations are hard to find and/or create that achieve the message / emotion we are trying to communicate. I don't have any good answers for this but I will say we can hire both animators and illustrators if we need to. All you have to do is communicate the effect in the website design with some simpler version maybe not the end illustration or animation itself. Added Wednesday, June 7, 2017

• Sex appeal and a sense of humor. Copy that makes people excited and clairvoyant about our potential.
• Boring renditions of other non-inspiring websites

```html
<!DOCTYPE html>
<html lang="en">
<head>
<meta charset="utf-8">
<title>Plumvessel — How engagement happens</title>
<link href="https://fonts.googleapis.com/css2?family=Roboto:ital,wght@0,300;0,400;0,500;0,700;1,300&display=swap" rel="stylesheet">
<style>
:root{
  --blue:#1aa3ec;
  --blue-dark:#0f8fd6;
  --band:#3fa9e4;
  --green:#5cb85c;
  --green-deep:#4aa84e;
  --ink:#333b44;
  --muted:#8a939c;
  --line:#e3e7eb;
  --grey-bg:#eef0f3;
  --white:#ffffff;
  --teal:#2f5f6b;
}
*{box-sizing:border-box;margin:0;padding:0}
html,body{width:1200px;height:3930px;overflow:hidden}
body{font-family:"Roboto",Arial,sans-serif;color:var(--ink);background:var(--white);position:relative}
.abs{position:absolute}
.btn{display:inline-block;font-size:13px;letter-spacing:.5px;padding:11px 26px;text-transform:uppercase}
.btn-solid{background:var(--blue);color:var(--white)}
.btn-line{border:1px solid var(--blue);color:var(--blue);background:var(--white)}
.para{font-size:12px;line-height:20px;color:var(--muted)}

/* hero */
.hero{top:0;left:0;width:1200px;height:510px;overflow:hidden}
.hero-photo{position:absolute;left:0;top:0;width:1200px;height:510px;background:linear-gradient(180deg,#ffffff 0%,#f2f2f2 30%,#c9b8a6 55%,#6c7783 80%,#4e5660 100%)}
.hero-fade{position:absolute;left:0;top:0;width:1200px;height:510px;background:linear-gradient(180deg,rgba(255,255,255,.95) 0%,rgba(255,255,255,.7) 30%,rgba(255,255,255,0) 55%)}
.nav{position:absolute;top:0;left:0;width:1200px;height:84px}
.brand{position:absolute;left:160px;top:26px;display:flex;align-items:center;gap:8px;font-size:22px;font-weight:500;color:var(--green)}
.brand i{display:block;width:18px;height:18px;border-radius:50%;background:var(--green)}
.menu{position:absolute;left:470px;top:38px;display:flex;gap:28px;font-size:11px;color:var(--ink)}
.menu .active{color:var(--blue)}
.nav-btns{position:absolute;left:872px;top:28px;display:flex;gap:12px}
.nav-btns span{font-size:12px;padding:7px 14px;border:1px solid var(--green);color:var(--green)}
.hero-title{position:absolute;left:158px;top:112px;font-size:32px;line-height:40px;font-weight:500;color:var(--blue)}
.hero-lead{position:absolute;left:510px;top:115px;width:520px;font-size:19px;line-height:26px;color:#2d3640}

.mission{top:510px;left:0;width:1200px;height:80px;background:var(--blue);color:var(--white)}
.mission .small{position:absolute;left:160px;top:18px;font-size:13px}
.mission .big{position:absolute;left:160px;top:38px;font-size:20px}
.mission .btn{position:absolute;left:803px;top:22px;background:var(--white);color:var(--blue);font-size:12px;padding:10px 30px;text-transform:none}

/* features */
.features{top:590px;left:0;width:1200px;height:550px}
.features h2{position:absolute;left:160px;top:95px;width:360px;font-size:21px;line-height:27px;font-weight:400}
.features .intro{position:absolute;left:160px;top:155px;width:360px;font-size:11px;line-height:17px}
.illus{position:absolute;left:165px;top:245px;width:285px;height:230px;border-radius:6px;background:radial-gradient(circle at 50% 55%,#f3e0cf 0%,#e9c9a9 40%,#ffffff 75%)}
.feat{position:absolute;width:200px}
.feat.hl{background:var(--blue);color:var(--white);padding:30px 22px;height:170px;box-shadow:0 10px 20px rgba(0,0,0,.12)}
.feat .ic{width:44px;height:44px;margin-bottom:12px}
.feat h3{font-size:11px;font-weight:500;text-transform:uppercase;margin-bottom:4px}
.feat p{font-size:11px;line-height:17px;color:var(--muted)}
.feat.hl p{color:var(--white)}

/* what we do */
.whatwedo{top:1140px;left:0;width:1200px;height:340px;background:var(--band);overflow:hidden}
.whatwedo .bgimg{position:absolute;inset:0;background:linear-gradient(180deg,rgba(255,255,255,.08),rgba(255,255,255,.22))}
.whatwedo h2{position:absolute;top:38px;width:1200px;text-align:center;color:var(--white);font-size:32px;font-weight:300;letter-spacing:1px}
.service{position:absolute;top:120px;width:176px;height:176px;border-radius:50%;background:var(--white);box-shadow:0 6px 18px rgba(0,0,0,.15);text-align:center}
.service .dot{width:84px;height:84px;border-radius:50%;background:var(--blue);margin:28px auto 10px;display:flex;align-items:center;justify-content:center}
.service span{font-size:17px;font-style:italic;font-weight:300;color:var(--blue)}

/* software */
.software{top:1480px;left:0;width:1200px;height:630px}
.app{position:absolute;left:160px;top:120px;width:420px;height:370px;background:var(--white);box-shadow:0 6px 18px rgba(0,0,0,.12);overflow:hidden}
.app .side{position:absolute;left:0;top:0;width:145px;height:370px;background:var(--teal)}
.app .side .logo{height:36px;background:var(--white);font-size:11px;color:var(--green);padding:12px 10px}
.app .side div.item{font-size:9px;color:#cfe2e6;padding:10px 12px;border-bottom:1px solid rgba(255,255,255,.08)}
.app .side div.on{background:rgba(255,255,255,.12)}
.app .main{position:absolute;left:145px;top:0;right:0;bottom:0;background:#f5f7f8}
.app .bar{height:36px;background:var(--white);font-size:10px;padding:12px;color:var(--muted)}
.app .filter{font-size:9px;color:var(--muted);padding:10px 12px;display:flex;gap:8px}
.app .filter b{font-weight:400;border:1px solid var(--line);background:var(--white);padding:2px 18px 2px 6px}
.card{position:absolute;width:190px;background:var(--white);box-shadow:0 3px 8px rgba(0,0,0,.1);font-size:8px;color:var(--muted)}
.card .hd{padding:6px 8px;border-bottom:1px solid var(--line)}
.card .row{display:flex;align-items:center;gap:8px;padding:7px 8px;color:var(--ink)}
.card .row i{width:22px;height:22px;border-radius:50%;background:#c7ccd1;display:block}
.software h2{position:absolute;left:660px;top:175px;font-size:21px;line-height:28px;font-weight:400}
.software .para{position:absolute;left:660px;top:250px;width:380px;font-size:11px;line-height:20px}

/* testimonial */
.quote{top:2110px;left:0;width:1200px;height:270px;background:var(--grey-bg);text-align:center}
.quote h3{position:absolute;top:55px;width:1200px;font-size:19px;font-weight:400;color:var(--blue)}
.quote blockquote{position:absolute;top:100px;width:1200px;font-size:32px;font-weight:300;font-style:italic;color:#3a4048}
.quote .who{position:absolute;top:155px;width:1200px;font-size:11px;font-weight:700;letter-spacing:.5px;line-height:16px}
.quote .who em{font-style:normal;color:var(--blue);font-weight:400}
.dots{position:absolute;width:1200px;display:flex;justify-content:center;gap:8px}
.dots i{width:9px;height:9px;border-radius:50%;background:#cfd4d9;display:block}
.dots i.on{background:var(--blue)}

/* how it works */
.how{top:2380px;left:0;width:1200px;height:600px}
.how h3{position:absolute;top:62px;width:1200px;text-align:center;font-size:19px;font-weight:300;color:#6b737b}
.sched{position:absolute;background:var(--white);box-shadow:0 6px 18px rgba(0,0,0,.15);font-size:10px;color:var(--muted)}
.sched .top{height:20px;background:var(--blue)}
.slot{border:1px solid var(--line);text-align:center;padding:7px 0;font-size:10px;color:var(--ink)}
.slot.sel{background:var(--blue);color:var(--white);border-color:var(--blue)}
.slot.dim{background:#c7ccd1;color:var(--white);border-color:#c7ccd1}

/* team band */
.team{top:2980px;left:0;width:1200px;height:325px;background:linear-gradient(90deg,#6cc36a,var(--green-deep) 50%,#6cc36a);text-align:center;color:var(--white)}
.team p{position:absolute;top:95px;width:1200px;font-size:22px;line-height:32px;font-weight:300}
.team .btns{position:absolute;top:170px;width:1200px;display:flex;justify-content:center;gap:30px}
.team .btns span{font-size:12px;padding:11px 45px}
.team .b1{background:var(--white);color:var(--green)}
.team .b2{border:1px solid var(--white)}

/* clients */
.clients{top:3305px;left:0;width:1200px;height:140px;display:flex;justify-content:center;align-items:center;gap:38px}
.clients span{font-size:13px;font-weight:700;color:#2a3a5a}

/* updates */
.updates{top:3445px;left:0;width:1200px;height:180px}
.col{position:absolute;top:12px;width:260px}
.col h4{font-size:14px;font-weight:500;color:var(--blue);margin-bottom:6px}
.col p,.col li{font-size:10px;line-height:16px;color:var(--ink)}
.col ul{list-style:none}
.col a{font-size:10px;color:var(--blue);text-decoration:none}

/* footer */
.footer{top:3625px;left:0;width:1200px;height:305px;background:var(--grey-bg)}
.footer .brand{top:58px}
.footer .about{position:absolute;left:160px;top:115px;width:560px;font-size:11px;line-height:16px;color:var(--ink)}
.footer .fbtn{position:absolute;left:160px;top:170px;display:flex;gap:10px}
.footer .fbtn span{font-size:10px;padding:7px 14px}
.footer .links{position:absolute;left:765px;top:115px;display:flex;gap:70px;font-size:9px;color:var(--muted)}
.footer .sub{position:absolute;left:755px;top:172px;display:flex;gap:20px}
.footer .sub input{width:170px;height:26px;border:none;border-bottom:1px solid #cfd4d9;background:transparent;font:10px "Roboto",sans-serif;color:var(--muted)}
.footer .sub span{font-size:10px;padding:6px 16px;border:1px solid var(--blue);color:var(--blue);background:var(--white)}
.footer .rule{position:absolute;left:160px;top:230px;width:880px;border-top:1px solid #d9dde1}
.footer .copy{position:absolute;left:160px;top:250px;font-size:10px;color:var(--muted)}
.footer .legal{position:absolute;left:645px;top:250px;display:flex;gap:26px;font-size:10px;color:var(--muted)}
.footer .social{position:absolute;left:940px;top:246px;display:flex;gap:18px}
.footer .social i{width:14px;height:14px;border-radius:50%;background:#4a5560;display:block}
</style>
</head>
<body>

<section class="abs hero">
  <div class="hero-photo" role="img" aria-label="Photo of a team of colleagues gathered around a table talking and laughing"></div>
  <div class="hero-fade"></div>
  <nav class="nav">
    <div class="brand"><i></i>Plumvessel</div>
    <div class="menu"><span class="active">Home</span><span>Product</span><span>About</span><span>Library</span><span>Careers</span><span>Contact</span></div>
    <div class="nav-btns"><span>Register Now</span><span>Login</span></div>
  </nav>
  <h1 class="hero-title">HOW ENGAGEMENT<br>HAPPENS</h1>
  <p class="hero-lead">Plumvessel helps increase face-to-face engagement in your communities and groups with custom built solutions, training, consulting, and tools.</p>
</section>

<section class="abs mission">
  <div class="small">How we're going to change the world by</div>
  <div class="big">connecting people in-person</div>
  <span class="btn">Request Consultation</span>
</section>

<section class="abs features">
  <h2>Increase face-to-face engagement in your communities and groups</h2>
  <p class="intro para">Lorem Ipsum is simply dummy text of the printing and typesetting industry. Lorem Ipsum has been the industry's standard dummy text ever since the 1500s, when an unknown printer took a galley of type and scrambled it to make a type specimen book.</p>
  <div class="illus" role="img" aria-label="Cartoon illustration of two friends chatting over coffee at a small table"></div>

  <div class="feat hl" style="left:565px;top:75px">
    <svg class="ic" viewBox="0 0 44 44"><circle cx="22" cy="22" r="20" fill="none" stroke="#fff" stroke-width="1.5"/><circle cx="22" cy="22" r="3" fill="#fff"/><circle cx="14" cy="16" r="2" fill="#fff"/><circle cx="30" cy="16" r="2" fill="#fff"/><circle cx="22" cy="31" r="2" fill="#fff"/></svg>
    <h3>Simplify face-to-face meetings</h3>
    <p>Lorem Ipsum is simply dummy text of the printing.</p>
  </div>
  <div class="feat" style="left:835px;top:95px">
    <svg class="ic" viewBox="0 0 44 44"><circle cx="22" cy="22" r="20" fill="none" stroke="#1aa3ec" stroke-width="1.5"/><circle cx="22" cy="15" r="3" fill="#1aa3ec"/><circle cx="15" cy="27" r="3" fill="#1aa3ec"/><circle cx="29" cy="27" r="3" fill="#1aa3ec"/></svg>
    <h3>Maximize collaboration</h3>
    <p>Lorem Ipsum is simply dummy text of the printing and typesetting industry.</p>
  </div>
  <div class="feat" style="left:590px;top:300px">
    <svg class="ic" viewBox="0 0 44 44"><circle cx="22" cy="22" r="20" fill="none" stroke="#1aa3ec" stroke-width="1.5"/><path d="M13 22h18M22 13v18" stroke="#1aa3ec" stroke-width="2"/></svg>
    <h3>Enhance interactions</h3>
    <p>Lorem Ipsum is simply dummy text of the printing and typesetting industry.</p>
  </div>
  <div class="feat" style="left:835px;top:300px">
    <svg class="ic" viewBox="0 0 44 44"><circle cx="22" cy="22" r="20" fill="none" stroke="#1aa3ec" stroke-width="1.5"/><path d="M22 12l9 10-9 10-9-10z" fill="none" stroke="#1aa3ec" stroke-width="2"/></svg>
    <h3>Help people build relationships</h3>
    <p>Lorem Ipsum is simply dummy text of the printing.</p>
  </div>
</section>

<section class="abs whatwedo">
  <div class="bgimg" role="img" aria-label="Faint backdrop of hands holding drawn smiley faces"></div>
  <h2>WHAT WE DO</h2>
  <div class="service" style="left:161px">
    <div class="dot"><svg width="44" height="44" viewBox="0 0 44 44"><path d="M22 6a11 11 0 0 0-6 20v5h12v-5a11 11 0 0 0-6-20z" fill="none" stroke="#fff" stroke-width="2.5"/><path d="M17 35h10M18 39h8" stroke="#fff" stroke-width="2.5"/></svg></div>
    <span>Solutions</span>
  </div>
  <div class="service" style="left:418px">
    <div class="dot"><svg width="44" height="44" viewBox="0 0 44 44"><path d="M8 14h9a4 4 0 1 1 8 0h9v9a4 4 0 1 0 0 8v7H8z" fill="#fff"/></svg></div>
    <span>Consulting</span>
  </div>
  <div class="service" style="left:632px">
    <div class="dot"><svg width="44" height="44" viewBox="0 0 44 44"><rect x="14" y="8" width="24" height="18" fill="none" stroke="#fff" stroke-width="2.5"/><circle cx="9" cy="18" r="4" fill="#fff"/><path d="M4 38v-9a5 5 0 0 1 10 0v9z" fill="#fff"/></svg></div>
    <span>Training</span>
  </div>
  <div class="service" style="left:855px">
    <div class="dot"><svg width="44" height="44" viewBox="0 0 44 44"><path d="M10 34L30 14M14 10l20 20" stroke="#fff" stroke-width="4" stroke-linecap="round"/><circle cx="32" cy="12" r="5" fill="none" stroke="#fff" stroke-width="2.5"/></svg></div>
    <span>Tools</span>
  </div>
</section>

<section class="abs software">
  <div class="app">
    <div class="side">
      <div class="logo">Plumvessel</div>
      <div class="item">Availability</div>
      <div class="item on">Meetings</div>
      <div class="item">Groups</div>
      <div class="item">More</div>
    </div>
    <div class="main">
      <div class="bar">Meetings</div>
      <div class="filter">Filter by <b>Select</b><b>Start date</b></div>
      <div class="card" style="left:10px;top:150px">
        <div class="hd">Date: 2017-06-20</div>
        <div class="row"><i></i>Tomas Reyes</div>
        <div class="row"><i></i>Priya Anand</div>
      </div>
      <div class="card" style="left:220px;top:150px">
        <div class="hd">Date: 2017-06-21</div>
        <div class="row"><i></i>Lena</div>
        <div class="row"><i></i>Amos</div>
      </div>
      <div class="card" style="left:10px;top:270px">
        <div class="hd">Date: 2017-06-22</div>
        <div class="row"><i></i>Greta Lund</div>
        <div class="row"><i></i>Omar Feldt</div>
      </div>
      <div class="card" style="left:220px;top:270px">
        <div class="hd">Date: 2017-06-23</div>
        <div class="row"><i></i>Cora</div>
        <div class="row"><i></i>Ivo</div>
      </div>
    </div>
  </div>
  <h2>We're building software<br>that connects people in person</h2>
  <p class="para">Lorem Ipsum is simply dummy text of the printing and typesetting industry. Lorem Ipsum has been the industry's standard dummy text ever since the 1500s, when an unknown printer took a galley of type and scrambled it to make a type specimen book. It has survived not only five centuries, but also the leap into electronic typesetting, remaining essentially unchanged. It was popularised in the 1960s with the release of printed sheets containing sample passages, and more recently with desktop publishing software carrying many versions of Lorem Ipsum.</p>
</section>

<section class="abs quote">
  <h3>What Our Customer Say's:</h3>
  <blockquote>&ldquo;10 times better than the last mentor scheduling tool.&rdquo;</blockquote>
  <div class="who">DALE HARKER | UX Consultant<br>Founder <em>Kelvo</em></div>
  <div class="dots" style="top:222px"><i></i><i class="on"></i><i></i></div>
</section>

<section class="abs how">
  <h3>Thats how Plumvessel works</h3>
  <div class="sched" style="left:340px;top:140px;width:150px;height:270px">
    <div class="top"></div>
    <div style="padding:14px 10px;display:grid;gap:10px">
      <div>Mon, Jun 19, 2017</div>
      <div class="slot">12:00pm</div><div class="slot">12:45pm</div><div class="slot">1:00pm</div><div class="slot">1:30pm</div><div class="slot dim">2:00pm</div>
    </div>
  </div>
  <div class="sched" style="left:710px;top:140px;width:150px;height:270px">
    <div class="top"></div>
    <div style="padding:14px 10px;display:grid;gap:10px">
      <div>&nbsp;</div>
      <div class="slot">1:00pm</div><div class="slot">12:45pm</div><div class="slot">1:15pm</div><div class="slot">1:45pm</div>
    </div>
  </div>
  <div class="sched" style="left:460px;top:115px;width:275px;height:345px;z-index:2">
    <div class="top" style="height:24px"></div>
    <div style="padding:10px 12px">
      <div style="text-align:center;margin-bottom:12px">Noel's availability</div>
      <div style="margin-bottom:10px;color:var(--ink)">Mon, Jun 19, 2017</div>
      <div class="slot sel" style="margin-bottom:8px">12:00pm</div>
      <div style="display:grid;grid-template-columns:1fr 1fr 1fr;gap:6px;margin-bottom:10px">
        <div class="slot">30 mins</div><div class="slot sel">45 mins</div><div class="slot">1 hour</div>
      </div>
      <div style="display:grid;grid-template-columns:1fr 1fr;gap:8px">
        <div class="slot">12:15pm</div><div class="slot">12:30pm</div>
        <div class="slot">12:45pm</div><div class="slot">1:00pm</div>
        <div class="slot">1:15pm</div><div class="slot">1:30pm</div>
        <div class="slot dim">1:45pm</div><div class="slot dim">2:00pm</div>
      </div>
    </div>
  </div>
  <div class="dots" style="top:495px"><i></i><i class="on"></i><i></i></div>
</section>

<section class="abs team" role="img" aria-label="Green tinted photo of colleagues smiling while working together">
  <p>Because it takes the perfect team<br>to bring great innovations to life</p>
  <div class="btns"><span class="b1">REQUEST DEMO</span><span class="b2">DOWNLOAD BROCHURE</span></div>
</section>

<section class="abs clients">
  <span>Northgard</span><span>Tradewell</span><span>Halvorn</span><span>Brightmoor Systems</span><span>Corvane</span><span>Westbury</span><span>Skyreach Air</span><span>Falk Drilling</span>
</section>

<section class="abs updates">
  <div class="col" style="left:160px">
    <h4>Latest News</h4>
    <p>07-06-2017</p>
    <p>Lorem Ipsum is simply dummy text of the printing and typesetting industry. Lorem Ipsum has been the industry's standard dummy text ever since the 1500s</p>
    <a>Read More</a>
  </div>
  <div class="col" style="left:497px">
    <h4>Tutorials</h4>
    <ul><li>- Lorem Ipsum is simply dummy text of the</li><li>- Printing and typesetting industry.</li><li>- Lorem Ipsum has been the industry's standard</li><li>- Dummy text ever since the 1500s</li></ul>
  </div>
  <div class="col" style="left:795px">
    <h4>Case Studies:</h4>
    <p>Case 1</p>
    <p>Lorem Ipsum is simply dummy text of the printing and typesetting industry. Lorem Ipsum has been the industry's standard dummy text ever since the 1500s</p>
    <a>Read More</a>
  </div>
</section>

<footer class="abs footer">
  <div class="brand"><i></i>Plumvessel</div>
  <p class="about">Lorem Ipsum is simply dummy text of the printing and typesetting industry. Lorem Ipsum has been the industry's standard dummy text ever since the 1500s</p>
  <div class="fbtn"><span class="btn-solid">REQUEST DEMO</span><span class="btn-line">DOWNLOAD BROCHURE</span></div>
  <div class="links"><span>CONTACT</span><span>ABOUT</span><span>IMPRESSUM</span></div>
  <div class="sub"><input type="text" placeholder="Your email address"><span>SUBSCRIBE</span></div>
  <div class="rule"></div>
  <div class="copy">&copy; 2017 Plumvessel Inc All rights reserved | Plumvessel&reg; is a registered trademark of Plumvessel Inc</div>
  <div class="legal"><span>Blog</span><span>Press</span></div>
  <div class="social"><i></i><i></i><i></i></div>
</footer>

</body>
</html>
```